Book Cover: Quiet Harbor: Small Ceremonies For The Restless Soul

I would like a full cover spread- front, back and spine as well as a stand alone front cover for Kindle for the book. Design a cover that mirrors the profound depth and dynamic energy of 'Quiet Harbor.' Envision a visual tapestry that draws readers into a transformative journey, where spirituality and self-care unite. Explore vibrant colors, intricate textures, and a sense of inner radiance that beckons readers to explore the book's rich wisdom within. See images for design inspiration attached. Even though some of the images are cartoon, I'd like the cover to be more serious than playful and very elegant.

About this book (back cover copy)
Are you ready to embark on a transformative journey and elevate your daily existence? "Quiet Harbor" is a treasure trove of practical yet profound rituals and wisdom from renowned self-care, healing, and spirituality experts.

Within these pages, you'll uncover a tapestry of guidance and insight from some of the world's most respected mentors. Their collective wisdom is your key to creating a sacred sanctuary within your everyday life.

From invigorating morning rituals to meditative practices, empowering affirmations, and transformative energy healing, you'll find a rich tapestry of tools to nurture a deeper connection with yourself and the universe.

Whether you're a seasoned practitioner or a newcomer to the world of self-care and spirituality, "Quiet Harbor" is your trusted companion on the journey to transform your life and elevate your daily experience. Open this book today and start your sacred, fulfilling adventure.

Colors
0094D4
00A9DD
6FCCEA
C7EBF8
E9F6FB
E54698
E96AAD
F1A4CE
F9D9EA
FCEFF6
6B429C
8869AF
B7A5CE
E3DAEB
F3F0F8

Requirements
Must have
• Title: Quiet Harbor: Subtitle: Small Ceremonies For The Restless Soul Name of Publisher: Lantern Bough Publishing- Logo on the back Back cover copy

```html
<!DOCTYPE html>
<html lang="en">
<head>
<meta charset="utf-8">
<title>Quiet Harbor – Cover Spread</title>
<link rel="stylesheet" href="https://fonts.googleapis.com/css2?family=Sacramento&family=Crimson+Text:ital,wght@0,400;0,700;1,400;1,700&display=swap">
<style>
  :root {
    --stage: #1f1f1f;
    --paper: #ffffff;
    --gold: #b48f3e;
    --ink: #1b1b1b;
  }
  * { margin: 0; padding: 0; box-sizing: border-box; }
  html, body {
    width: 1200px; height: 1200px; overflow: hidden;
    background: var(--stage);
  }
  .spread {
    position: absolute; left: 30px; top: 195px;
    width: 1140px; height: 809px;
    background: var(--paper);
    display: flex;
  }
  .back-cover { position: relative; width: 538px; height: 100%; }
  .spine { position: relative; width: 61px; height: 100%; }
  .front-cover { position: relative; width: 541px; height: 100%; overflow: hidden; }

  .script { font-family: "Sacramento", cursive; color: var(--gold); font-weight: 400; }
  .serif { font-family: "Crimson Text", serif; }

  /* Back cover */
  .back-title {
    position: absolute; top: 46px; left: 0; width: 100%;
    text-align: center; font-size: 88px; line-height: 1;
  }
  .back-subtitle {
    position: absolute; top: 162px; left: 0; width: 100%;
    text-align: center; font-size: 22px; color: var(--gold);
    font-style: italic;
  }
  .subtitle strong { font-style: normal; font-weight: 700; }
  .back-copy {
    position: absolute; top: 214px; left: 66px; width: 410px;
    text-align: center; color: var(--ink);
    font-size: 15.3px; line-height: 20px;
  }
  .back-copy p + p { margin-top: 20px; }
  .back-copy b { font-weight: 700; }
  .publisher-mark {
    position: absolute; top: 718px; left: 58px;
    font-size: 21px; line-height: 28px; color: var(--ink);
    text-align: center; letter-spacing: 0.5px;
  }

  /* Spine */
  .spine-text {
    position: absolute; top: 40px; left: 0; width: 100%; height: 760px;
    writing-mode: vertical-rl;
    display: flex; align-items: center; gap: 18px;
  }
  .spine-title { font-size: 42px; line-height: 1; }
  .spine-subtitle { font-size: 18px; color: var(--gold); font-style: italic; white-space: nowrap; }
  .spine-publisher { font-size: 17px; color: var(--ink); white-space: nowrap; }

  /* Front cover */
  .front-art { position: absolute; inset: 0; }
  .front-title {
    position: absolute; left: 24px; top: 430px;
    font-size: 190px; line-height: 1; white-space: nowrap;
  }
  .front-title-second {
    position: absolute; left: 40px; top: 612px;
    font-size: 105px; line-height: 1; white-space: nowrap;
  }
  .front-subtitle {
    position: absolute; left: 338px; top: 676px; width: 190px;
    text-align: center; font-size: 21px; line-height: 24px;
    color: var(--gold); font-style: italic;
  }
</style>
</head>
<body>
<main class="spread">

  <section class="back-cover">
    <h2 class="back-title script">Quiet Harbor</h2>
    <p class="back-subtitle subtitle serif">Small Ceremonies for <strong>The Restless Soul</strong></p>
    <div class="back-copy serif">
      <p><b>Are you ready to embark on a transformative journey and elevate your daily existence?</b> <i>"Quiet Harbor"</i> is a treasure trove of practical yet profound rituals and wisdom from renowned self-care, healing, and spirituality experts.</p>
      <p>Within these pages, you'll uncover a tapestry of guidance and insight from some of the world's most respected mentors. Their collective wisdom is your key to creating a sacred sanctuary within your everyday life.</p>
      <p>From invigorating morning rituals to meditative practices, empowering affirmations, and transformative energy healing, you'll find a rich tapestry of tools to nurture a deeper connection with yourself and the universe.</p>
      <p>Whether you're a seasoned practitioner or a newcomer to the world of self-care and spirituality, "Quiet Harbor" is your trusted companion on the journey to transform your life and elevate your daily experience. Open this book today and start your sacred, fulfilling adventure.</p>
    </div>
    <p class="publisher-mark serif">Lantern Bough<br>Publishing</p>
  </section>

  <section class="spine">
    <div class="spine-text">
      <span class="spine-title script">Quiet Harbor</span>
      <span class="spine-subtitle serif">Small Ceremonies for The Restless Soul</span>
      <span class="spine-publisher serif">Lantern Bough Publishing</span>
    </div>
  </section>

  <section class="front-cover">
    <svg class="front-art" viewBox="0 0 541 809" width="541" height="809"
         role="img" aria-label="Watercolour illustration of a woman's profile silhouette within overlapping rainbow colour washes">
      <defs>
        <linearGradient id="wash" x1="0" y1="0" x2="1" y2="1">
          <stop offset="0" stop-color="#1f8f86"/>
          <stop offset="0.2" stop-color="#2b4f9c"/>
          <stop offset="0.4" stop-color="#e8543a"/>
          <stop offset="0.55" stop-color="#f2c423"/>
          <stop offset="0.75" stop-color="#4a9a3a"/>
          <stop offset="1" stop-color="#1f8f86"/>
        </linearGradient>
        <linearGradient id="fade" x1="0" y1="0" x2="0" y2="1">
          <stop offset="0.7" stop-color="#ffffff" stop-opacity="0"/>
          <stop offset="1" stop-color="#ffffff" stop-opacity="1"/>
        </linearGradient>
      </defs>
      <path d="M20 0 L541 0 L541 460 C470 420 400 440 330 560 C300 520 230 470 160 380 C90 290 40 180 20 0 Z" fill="url(#wash)"/>
      <path d="M20 0 L541 0 L541 460 C470 420 400 440 330 560 C300 520 230 470 160 380 C90 290 40 180 20 0 Z" fill="url(#fade)"/>
    </svg>
    <h1 class="front-title script">Quiet</h1>
    <p class="front-title-second script">Harbor</p>
    <p class="front-subtitle subtitle serif">Small Ceremonies for <strong>The Restless Soul</strong></p>
  </section>

</main>
</body>
</html>
```